Visitenkarten-Design für IT-Service
Zielgruppe
IT-Service
Zielgruppe sind mittelständische Unternehmen aus unterschiedlichen Branchen, die eine Betreuung ihre IT benötigen.
Die Visitenkarte darf sich gerne vom Standard abheben, ein 'Eyecatcher' wär schön
Aufgabenstellung
Es sollen auf der einen Seite das Logo und der Name und auf der anderen die notwendigen Information:
Firmenname: Kolvane GmbH und Logo
Berliner IT-Service
Personenname: Vorname Nachname
Funktion, zB: Geschäftsführer
Web: www.kolvane.de
Schriftart im Logo ist Expansiva https://www.glyphmarkt.example/de/expansiva.font

```html
<!DOCTYPE html>
<html lang="de">
<head>
<meta charset="utf-8">
<title>Kolvane – Visitenkarte</title>
<link rel="stylesheet" href="https://fonts.googleapis.com/css2?family=Varela+Round&display=swap">
<style>
  :root {
    --stage: #34444d;
    --paper: #ffffff;
    --navy: #233a6e;
    --navy-deep: #022441;
    --teal: #1b8bb4;
    --ink: #1b1f2a;
    --light: #e6e8ec;
    --font: "Varela Round", sans-serif;
  }
  * { box-sizing: border-box; margin: 0; padding: 0; }
  html, body {
    width: 1200px; height: 900px; overflow: hidden;
    background: var(--stage);
    font-family: var(--font);
  }
  .canvas {
    width: 1200px; height: 900px;
    display: flex; flex-direction: column; align-items: center; justify-content: center;
    gap: 40px;
  }
  .card {
    position: relative;
    width: 600px; height: 388px;
    border-radius: 22px;
    overflow: hidden;
    box-shadow: 0 14px 30px rgba(0,0,0,.35);
  }
  /* front */
  .card--front { background: var(--paper); }
  .brand {
    position: absolute; left: 68px; top: 150px;
    display: flex; align-items: center; gap: 14px;
  }
  .brand__mark { width: 28px; height: 28px; border-radius: 6px; background: var(--navy); }
  .brand__name { font-size: 30px; color: var(--navy); letter-spacing: 2px; }
  .divider {
    position: absolute; left: 296px; top: 42px;
    width: 4px; height: 168px; background: var(--navy);
  }
  .contact { position: absolute; left: 362px; top: 40px; color: var(--ink); }
  .contact__name { font-size: 30px; color: var(--teal); font-weight: 700; letter-spacing: .5px; line-height: 1; }
  .contact__role { font-size: 13px; color: var(--navy); margin-top: 3px; }
  .contact__address { font-size: 14px; line-height: 1.3; margin-top: 22px; }
  .contact__lines { font-size: 14px; line-height: 1.35; margin-top: 18px; padding-left: 6px; }
  .band-teal {
    position: absolute; left: 0; bottom: 0;
    width: 340px; height: 12px; background: var(--teal);
  }
  .web-tab {
    position: absolute; right: 0; bottom: 0;
    width: 262px; height: 52px;
    background: var(--navy);
    border-top-left-radius: 24px;
    color: var(--paper);
    font-size: 15px; letter-spacing: .3px;
    display: flex; align-items: center; justify-content: center;
  }
  /* back */
  .card--back { background: var(--navy-deep); border-radius: 0; }
  .card--back .brand {
    left: 50%; top: 50%; transform: translate(-50%, -50%);
    gap: 20px;
  }
  .card--back .brand__mark { width: 38px; height: 38px; border-radius: 8px; background: var(--light); }
  .card--back .brand__name { font-size: 42px; color: var(--light); letter-spacing: 3px; }
</style>
</head>
<body>
<main class="canvas">
  <section class="card card--front" aria-label="Visitenkarte Vorderseite">
    <div class="brand">
      <span class="brand__mark"></span>
      <span class="brand__name">Kolvane</span>
    </div>
    <div class="divider"></div>
    <div class="contact">
      <p class="contact__name">Mara Velden</p>
      <p class="contact__role">Director</p>
      <p class="contact__address">Lindauer Weg 12<br>10115 Berlin</p>
      <p class="contact__lines">T : 030-555 01 234<br>F : 030-555 01 235<br>M : name@kolvane.de</p>
    </div>
    <div class="band-teal"></div>
    <div class="web-tab">W : www.kolvane.de</div>
  </section>

  <section class="card card--back" aria-label="Visitenkarte Rückseite">
    <div class="brand">
      <span class="brand__mark"></span>
      <span class="brand__name">Kolvane</span>
    </div>
  </section>
</main>
</body>
</html>
```